website homepage design sample for tovelane.com.au

Hello, I am looking to update my website to be simpler and more modern and to include space for my upcoming online courses. Please review my website tovelane.com.au for an idea of me as a male psychologist, as well as my services. I would like it to be NOT too feminine. Target market is Men and women interested in couselling, life coaching, and online courses about relationships. Id like to keep the beach theme if possible but I am open to better ideas. thank you!

please see tovelane.com.au for my current wordpress website.

Target Market(s)

Men and Women

Industry/Entity Type

psychology

Number of Pages Required

1 page

Requirements
Must have
• An "Online Training" Menu that includes links to "Chart your Daily Rhythm" , "Lantern and Compass Workbook," "Bright Morning Program" "Should We Dance Before Dawn" "Building Quiet Harmony"

```html
<!DOCTYPE html>
<html lang="en">
<head>
<meta charset="utf-8">
<title>Tovelane – Gold Coast Psychologist</title>
<link href="https://fonts.googleapis.com/css2?family=Lato:wght@400;700;900&family=Montserrat:wght@600;700&display=swap" rel="stylesheet">
<style>
:root{
  --navy:#2f4b63;
  --teal:#2f9fc0;
  --teal-dark:#2585a8;
  --heading:#2b8db3;
  --text:#333c44;
  --muted:#5b6670;
  --pale:#eef5f8;
  --white:#ffffff;
}
*{box-sizing:border-box;margin:0;padding:0}
html,body{width:1200px;height:4804px;overflow:hidden}
body{position:relative;font-family:'Lato',sans-serif;color:var(--text);background:var(--white)}
.abs{position:absolute}
section,header,footer{position:absolute;left:0;width:1200px}
.btn{position:absolute;display:flex;align-items:center;justify-content:center;color:var(--white);font:700 13px 'Lato',sans-serif;letter-spacing:.3px;border-radius:3px}
.section-title{position:absolute;left:0;width:1200px;text-align:center;font:700 42px 'Lato',sans-serif;color:var(--heading);letter-spacing:.5px}
.rule{position:absolute;left:575px;width:50px;height:3px;background:var(--teal)}

/* header */
.site-header{top:0;height:100px;background:var(--white)}
.brand{left:110px;top:30px;display:flex;align-items:center;gap:12px}
.brand-mark{width:34px;height:34px;border-radius:50%;background:var(--teal)}
.brand-name{font:900 20px 'Lato',sans-serif;color:var(--teal);letter-spacing:.5px}
.nav{left:336px;top:41px;display:flex;gap:17px;font:400 13px 'Lato',sans-serif;color:var(--navy);white-space:nowrap}
.nav .active{color:var(--teal)}
.nav .has-menu::after{content:"";display:inline-block;margin-left:5px;border:4px solid transparent;border-top-color:var(--navy);vertical-align:-1px}
.nav-cta{left:913px;top:28px;width:175px;height:40px;background:var(--teal)}

/* hero */
.hero{top:100px;height:455px;background:
  linear-gradient(90deg,rgba(40,55,70,.55) 0%,rgba(40,55,70,.25) 35%,rgba(40,55,70,0) 60%),
  linear-gradient(180deg,#c2c4bd 0%,#ddc9a6 22%,#e9cfa0 30%,#9fa7a4 36%,#c9a77f 48%,#d9b48a 65%,#b98b5c 100%)}
.hero-title{left:110px;top:62px;font:700 37px 'Lato',sans-serif;color:var(--white)}
.hero-sub{left:114px;top:112px;font:400 19px 'Lato',sans-serif;color:var(--white)}
.hero-avail{left:114px;top:158px;font:400 16px 'Lato',sans-serif;color:var(--white)}
.hero-copy{left:112px;top:193px;width:400px;font:400 14px/27px 'Lato',sans-serif;color:var(--white)}
.hero-btn{left:112px;top:354px;width:175px;height:40px;background:var(--teal)}

/* band */
.band{top:555px;height:453px;background:var(--navy);text-align:center}
.band-title{left:0;top:98px;width:1200px;font:700 41px/52px 'Montserrat',sans-serif;color:var(--white)}
.band-rule{left:575px;top:270px;width:50px;height:3px;background:var(--teal)}
.band-rebate{left:0;top:288px;width:1200px;font:700 28px 'Lato',sans-serif;color:#3fb4dc}
.band-tag{left:0;top:330px;width:1200px;font:400 29px 'Lato',sans-serif;color:var(--white)}

/* about */
.about{top:1008px;height:592px}
.about-lead{left:112px;top:176px;font:400 16px 'Lato',sans-serif;color:var(--text)}
.about-copy{left:112px;top:212px;width:510px;font:400 14.5px/30px 'Lato',sans-serif;color:var(--muted)}
.about-copy p{margin-bottom:6px}
.about-btn{left:112px;top:512px;width:176px;height:40px;background:linear-gradient(90deg,var(--teal-dark),#7ec6d4)}
.about-frame{left:722px;top:156px;width:350px;height:360px;border-radius:40px 0 0 0;background:linear-gradient(90deg,var(--teal),#7ec6d4)}
.about-photo{left:740px;top:172px;width:348px;height:360px;border-radius:40px 0 0 0;background:linear-gradient(180deg,#e4e4e4 0%,#d6cfca 35%,#c9a58e 60%,#8b8f9e 100%);border:3px solid var(--white)}

/* services */
.services{top:1600px;height:525px;background:var(--pale)}
.svc-card{position:absolute;top:152px;width:440px;height:306px;background:var(--white);box-shadow:0 2px 8px rgba(0,0,0,.06)}
.svc-photo{position:absolute;left:8px;top:8px;width:424px;height:196px}
.svc-label{position:absolute;left:0;top:226px;width:100%;text-align:center;font:400 20px/28px 'Lato',sans-serif;color:var(--text)}

/* self worth */
.worth{top:2125px;height:625px;background:linear-gradient(100deg,#6d97a6 0%,#2a9ec2 45%,#53b4cf 75%,#3a95b9 100%)}
.worth-title{top:60px;color:var(--white)}
.worth-photo{left:112px;top:195px;width:340px;height:355px;border-radius:0 38px 0 0;background:linear-gradient(180deg,#c9c6bb 0%,#9a9588 40%,#5b5f66 65%,#7a4e38 100%)}
.worth-copy{left:552px;top:190px;width:540px;font:400 14.5px/27px 'Lato',sans-serif;color:var(--white)}
.worth-copy p{margin-bottom:9px}
.worth-copy strong{color:var(--navy);font-weight:700}
.worth-btn{left:552px;top:512px;width:336px;height:38px;background:var(--navy);font-size:12.5px}

/* online courses */
.courses{top:2750px;height:522px}
.course-path{left:0;top:0}
.course{position:absolute;width:220px;text-align:center}
.course-icon{width:104px;height:104px;border-radius:50%;background:var(--navy);margin:0 auto;display:flex;align-items:center;justify-content:center}
.course-name{margin-top:22px;font:400 16.5px/28px 'Lato',sans-serif;color:var(--text)}
.course-name.hl{color:var(--heading)}

/* support */
.support{top:3272px;height:638px}
.sup-card{position:absolute;top:183px;width:232px;height:370px;border-radius:4px;overflow:hidden}
.sup-card span{position:absolute;left:0;top:240px;width:100%;text-align:center;font:700 20px/33px 'Lato',sans-serif;color:var(--white)}
.sup-arrow{position:absolute;top:348px;width:40px;height:40px}

/* objectives */
.objectives{top:3910px;height:585px}
.obj{position:absolute;left:112px;display:flex;gap:34px;font:400 16.5px/28px 'Lato',sans-serif;color:var(--text);width:500px}
.obj-num{position:relative;flex:0 0 28px;height:28px}
.obj-num i{position:absolute;left:0;top:8px;width:28px;height:28px;border-radius:50%;background:#a9dcea}
.obj-num b{position:absolute;left:16px;top:-6px;font:700 20px 'Lato',sans-serif;color:var(--navy)}
.obj-frame{left:760px;top:148px;width:325px;height:356px;background:#8fd0dd}
.obj-photo{left:738px;top:148px;width:340px;height:350px;background:linear-gradient(180deg,#c9c6bb 0%,#9a9588 40%,#5b5f66 65%,#7a4e38 100%)}
.badge{position:absolute;top:476px;height:56px;border-radius:6px}

/* footer */
.site-footer{top:4495px;height:309px;background:var(--navy);color:var(--white)}
.foot-col{position:absolute;top:48px;font:400 14.5px/27px 'Lato',sans-serif}
.foot-col h4{font:700 15.5px 'Lato',sans-serif;margin-bottom:14px;letter-spacing:.3px}
.copy{left:0;top:250px;width:1200px;text-align:center;font:400 14.5px 'Lato',sans-serif}
</style>
</head>
<body>

<header class="site-header">
  <div class="abs brand"><span class="brand-mark"></span><span class="brand-name">TOVELANE</span></div>
  <nav class="abs nav">
    <span class="active">HOME</span><span>ABOUT</span><span>SERVICES &amp; FEES</span><span class="has-menu">ONLINE TRAINING</span><span>BLOG</span><span>CONTACT</span><span>BOOKINGS</span>
  </nav>
  <a class="btn nav-cta">SELF ESTEEM COURSE</a>
</header>

<section class="hero" role="img" aria-label="Photo of a man walking alone along a beach at sunset">
  <h1 class="abs hero-title">TOVELANE</h1>
  <div class="abs hero-sub">Psychology Solutions + Your Choices</div>
  <div class="abs hero-avail">NEXT AVAILABLE APPOINTMENT: <b>WITHIN 7 DAYS</b></div>
  <p class="abs hero-copy">At Tovelane, we are focused on your mental wellness. Tovelane is open to anyone looking for an Online or Gold Coast Psychologist to help them overcome barriers and find fulfilment in their lives. We also offer do it yourself educational programs.</p>
  <a class="btn hero-btn">BOOK APPOINTMENT</a>
</section>

<section class="band">
  <h2 class="abs band-title">GOLD COAST PSYCHOLOGIST<br>ALSO OFFERING AUSTRALIA-WIDE<br>TELEHEALTH</h2>
  <div class="abs band-rule"></div>
  <div class="abs band-rebate">Health fund rebates available</div>
  <div class="abs band-tag">Experienced – Caring – Understanding – Effective – Affordable</div>
</section>

<section class="about">
  <h2 class="section-title" style="top:62px">ABOUT US</h2>
  <div class="rule" style="top:114px"></div>
  <p class="abs about-lead">An experienced Gold Coast Psychologist, also available online.</p>
  <div class="abs about-copy">
    <p>Unfortunately, we all go through periods of crisis in our lives. When we find ourselves struggling for an extended period, we can use bit of help to work through barriers that stand in our way. Counselling or psychotherapy can help. Contact Daniel, your Gold Coast Psychologist.</p>
    <p>Daniel has 15 years experience in providing counselling and psycho-therapy to people from all of walks of life. Daniel understands the different challenges that people of all backgrounds face in coming to seek help and has a variety of treatments to help.</p>
  </div>
  <a class="btn about-btn">ONLINE HELP</a>
  <div class="abs about-frame"></div>
  <div class="abs about-photo" role="img" aria-label="Portrait photo of the psychologist"></div>
</section>

<section class="services">
  <h2 class="section-title" style="top:62px">OUR SERVICES</h2>
  <div class="rule" style="top:112px"></div>
  <div class="svc-card" style="left:148px">
    <div class="svc-photo" role="img" aria-label="Photo of a woman on a video call with a therapist on a laptop" style="background:linear-gradient(100deg,#8a6d55 0%,#c9a687 35%,#b8b2aa 60%,#5b5d63 100%)"></div>
    <div class="svc-label">Phone or Video<br>Telehealth</div>
  </div>
  <div class="svc-card" style="left:612px">
    <div class="svc-photo" role="img" aria-label="Photo of a counselling session between two men" style="background:linear-gradient(100deg,#e4e6e4 0%,#b8bdb8 35%,#8e9a86 60%,#3e3f45 100%)"></div>
    <div class="svc-label">Anxiety &amp; Depression<br>Counselling</div>
  </div>
</section>

<section class="worth" role="img" aria-label="Soft blue bokeh water background">
  <h2 class="section-title worth-title">FINDING SELF WORTH</h2>
  <div class="abs worth-photo" role="img" aria-label="Photo of two men talking in a counselling session"></div>
  <div class="abs worth-copy">
    <p>Wondering where to start? Watch our free <strong>Self Worth Webinar</strong></p>
    <p>Wondering how your self Esteem stacks up? &nbsp;take our <strong>Assertiveness Quiz</strong>.</p>
    <p>Interested in a what psychotherapy can offer but not quite ready? Try our <strong>Self Esteem Course</strong></p>
    <p>Your Online or Gold Coast Psychologist should not only be about moving away from what makes you sad, but moving towards what makes you happy, resilient engaged and fulfilled. At Tovelane, Daniel combines evidence-based treatment from both mental illness and mental wellness fields to take you all the way from anxiety and depression to strength and success.</p>
  </div>
  <a class="btn worth-btn">5 STEPS CLOSER TO SELF ESTEEM ONLY $47</a>
</section>

<section class="courses">
  <h2 class="section-title" style="top:72px">ONLINE COURSES</h2>
  <div class="rule" style="top:124px"></div>
  <svg class="abs course-path" width="1200" height="522" viewBox="0 0 1200 522" aria-hidden="true">
    <path d="M220 222 C260 240 290 260 320 295 M420 295 C460 240 480 200 510 180 M650 240 C690 230 700 210 725 205 M850 290 C880 270 900 230 950 215" fill="none" stroke="#9aa3aa" stroke-width="2" stroke-dasharray="6 6"/>
    <circle cx="220" cy="222" r="4" fill="#9aa3aa"/><circle cx="510" cy="180" r="5" fill="#9aa3aa"/><circle cx="725" cy="205" r="5" fill="#9aa3aa"/>
  </svg>
  <div class="course" style="left:58px;top:186px"><div class="course-icon"><svg width="50" height="50" viewBox="0 0 50 50" fill="none" stroke="#fff" stroke-width="2"><circle cx="18" cy="12" r="6"/><path d="M8 36c0-8 4-13 10-13s10 5 10 13"/><rect x="28" y="28" width="16" height="10"/></svg></div><div class="course-name">Chart your Daily<br>Rhythm</div></div>
  <div class="course" style="left:260px;top:264px"><div class="course-icon"><svg width="50" height="50" viewBox="0 0 50 50" fill="none" stroke="#fff" stroke-width="2"><path d="M16 42V30c-6-4-7-12-3-18s14-7 19-2 5 12 1 16v16"/><circle cx="26" cy="20" r="5"/></svg></div><div class="course-name hl">Lantern and Compass<br>Workbook</div></div>
  <div class="course" style="left:470px;top:186px"><div class="course-icon"><svg width="50" height="50" viewBox="0 0 50 50" fill="none" stroke="#fff" stroke-width="2"><circle cx="25" cy="22" r="6"/><path d="M13 42c0-8 5-12 12-12s12 4 12 12M25 5v5M12 12l3 3M38 12l-3 3"/></svg></div><div class="course-name">Bright Morning<br>Program</div></div>
  <div class="course" style="left:670px;top:264px"><div class="course-icon"><svg width="50" height="50" viewBox="0 0 50 50" fill="none" stroke="#fff" stroke-width="2"><path d="M8 14l10 22 8-6M42 14L32 36l-8-6M18 36l7 6 7-6"/></svg></div><div class="course-name">Should We Dance<br>Before Dawn</div></div>
  <div class="course" style="left:893px;top:186px"><div class="course-icon"><svg width="50" height="50" viewBox="0 0 50 50" fill="none" stroke="#fff" stroke-width="2"><path d="M25 42L9 26a9 9 0 0 1 16-12 9 9 0 0 1 16 12z"/><path d="M17 26l6 5 10-10"/></svg></div><div class="course-name">Building Quiet<br>Harmony</div></div>
</section>

<section class="support">
  <h2 class="section-title" style="top:72px">TOVELANE SUPPORT</h2>
  <div class="rule" style="top:124px"></div>
  <svg class="sup-arrow" style="left:42px" viewBox="0 0 40 40" aria-hidden="true"><circle cx="20" cy="20" r="18" fill="none" stroke="#9aa3aa" stroke-width="2"/><path d="M28 20H12m6-6l-6 6 6 6" fill="none" stroke="#9aa3aa" stroke-width="2"/></svg>
  <div class="sup-card" style="left:113px;background:linear-gradient(180deg,#8f8a70 0%,#a08870 40%,#5a4d42 100%)" role="img" aria-label="Photo of a thoughtful man for psychological counselling"><span>Psychological<br>Counselling</span></div>
  <div class="sup-card" style="left:360px;background:linear-gradient(180deg,#6e7a82 0%,#4f5c66 45%,#2f3a44 100%)" role="img" aria-label="Photo of a video webinar grid on a laptop"><span>FREE Self<br>Esteem Webinar</span></div>
  <div class="sup-card" style="left:608px;background:linear-gradient(180deg,#c8cfd2 0%,#a5a39c 35%,#8a6a52 100%)" role="img" aria-label="Photo of a woman with flowing hair in sunlight"><span>Self Esteem Course<br>only $47</span></div>
  <div class="sup-card" style="left:856px;background:linear-gradient(180deg,#7c8a92 0%,#56636c 45%,#36414a 100%)" role="img" aria-label="Photo of a hand choosing an answer on a quiz screen"><span>FREE Assertiveness<br>QUIZ</span></div>
  <svg class="sup-arrow" style="left:1116px" viewBox="0 0 40 40" aria-hidden="true"><circle cx="20" cy="20" r="18" fill="none" stroke="#222" stroke-width="2"/><path d="M12 20h16m-6-6l6 6-6 6" fill="none" stroke="#222" stroke-width="2"/></svg>
</section>

<section class="objectives">
  <h2 class="section-title" style="top:54px">TOVELANE HAS V3 OBJECTIVES</h2>
  <div class="rule" style="top:114px"></div>
  <div class="obj" style="top:186px"><span class="obj-num"><i></i><b>1</b></span><span>Alleviate distress.</span></div>
  <div class="obj" style="top:246px"><span class="obj-num"><i></i><b>2</b></span><span>Take the next step in helping you create a fulfilling, meaningful and enjoyable life through coaching and positive psychology.</span></div>
  <div class="obj" style="top:352px"><span class="obj-num"><i></i><b>3</b></span><span>Learn, implement and habitualise advanced performance strategies for lasting change.</span></div>
  <div class="badge" style="left:118px;width:130px;background:#1f9a4a"></div>
  <div class="badge" style="left:282px;width:106px;background:#e8a83a"></div>
  <div class="abs obj-frame"></div>
  <div class="abs obj-photo" role="img" aria-label="Photo of two men talking in a counselling session"></div>
</section>

<footer class="site-footer">
  <div class="foot-col" style="left:112px"><h4>DANIEL HAYES</h4>Registered Psychologist<br>Psychology Society Member<br>Accredited Life Coach<br>Trauma Therapy Assoc. Member</div>
  <div class="foot-col" style="left:378px"><h4>CONTACT US</h4><b>48 Harbour Lane, Southport</b><br>0400 000 123<br>Fax. (07) 3000 0199<br>8:00am - 7:00pm (appt. Only)</div>
  <div class="foot-col" style="left:692px"><h4>HELPFUL LINKS</h4>Home<br>About Us<br>Services &amp; Fees<br>Book Today</div>
  <div class="foot-col" style="left:910px"><h4>OUR SERVICES</h4>Anxiety and Depression<br>Anger Management<br>Dating and Relationships<br>Self Esteem<br>Trauma inc. EMDR</div>
  <div class="abs copy">2024 Tovelane. All Rights Reserved.</div>
</footer>

</body>
</html>
```